So the ones in the picture are my original cards that I came up with. 😅however I kinda messed up on two things, I missed spelled my name it should be Marcello Vandora as well as the email should be Marcellov@brightlanecrews.com. I would like to clean this card up and also make it pop! Something that people would remember me by and that screams DEMOLITION. As well as a card that give you a feeling of loyalty and trust. I would also like to change and remove junk hauling and add full demolition to replace it. These cards worked for a little while but I cant make that my image while handing these out. I would also like to only put down that we are located in Laguna Crest, CA, 92610 instead of the address on the card. Also if we can have a line that states Licensed, Bonded, & Insured. With out License # 4837215

Target Market(s)

Contractors and Home owners

Industry/Entity Type

Construction specialist in Demolition

Contact Information for Business Card

R Wrecking Selective Demolition & Full Demolition Kitchens AD Preparation Bathrooms Sheds Interiors & Exteriors Demo Digging And Much More Marcello Vandora Owner our city state and zip

Font styles to use
Serif
Sans Serif
Decorative

Colors
0054AA
0677BA
7BADD7
CADEEF
E8F1F8
0094D4
00A9DD
6FCCEA
C7EBF8
E9F6FB

Requirements
Must have
• License# 4837215
Nice to have
• Trying to go with a blue and white color scheme
Should not have
• Building construction

```html
<!DOCTYPE html>
<html lang="en">
<head>
<meta charset="utf-8">
<title>RK Wrecking Business Card</title>
<link rel="stylesheet" href="https://fonts.googleapis.com/css2?family=Montserrat:wght@700;800&family=Open+Sans:wght@400;600&family=Oswald:wght@500;600;700&display=swap">
<style>
  :root {
    --page: #e9edf2;
    --navy: #0b1e3d;
    --blue: #0054aa;
    --blue-mid: #0677ba;
    --sky: #0094d4;
    --sky-light: #7badd7;
    --mist: #e8f1f8;
    --ink: #1b1b1b;
    --white: #ffffff;
  }
  * { box-sizing: border-box; margin: 0; padding: 0; }
  html, body { width: 1200px; height: 780px; overflow: hidden; background: var(--page); }
  .canvas { position: relative; width: 1200px; height: 780px; }
  .card {
    position: absolute; top: 40px; width: 400px; height: 700px;
    border-radius: 30px; overflow: hidden;
    box-shadow: 0 8px 22px rgba(11, 30, 61, .22);
  }

  /* Back */
  .card-back { left: 150px; background: linear-gradient(160deg, var(--blue) 0%, var(--navy) 100%); }
  .back-stripe { position: absolute; left: 0; right: 0; bottom: 0; height: 28px; background: var(--sky); }
  .back-mark {
    position: absolute; left: 50%; top: 47%;
    transform: translate(-50%, -50%) rotate(-90deg);
    display: flex; flex-direction: column; align-items: flex-end; white-space: nowrap;
  }
  .back-name {
    font-family: "Oswald", sans-serif; font-weight: 700; font-size: 92px; line-height: 1;
    letter-spacing: 2px; color: var(--white); display: flex; align-items: center; gap: 18px;
  }
  .back-dot { width: 52px; height: 52px; border-radius: 50%; background: var(--sky); }
  .back-license {
    font-family: "Montserrat", sans-serif; font-weight: 800; font-size: 22px;
    color: var(--sky-light); letter-spacing: 1px; margin-top: 6px;
  }
  .back-trust {
    font-family: "Oswald", sans-serif; font-weight: 500; font-size: 18px;
    color: var(--white); letter-spacing: 2px; margin-top: 4px;
  }

  /* Front */
  .card-front { left: 650px; background: var(--white); text-align: center; font-family: "Open Sans", sans-serif; color: var(--ink); }
  .header {
    position: absolute; left: 0; top: 0; width: 400px; height: 145px;
    background: linear-gradient(120deg, var(--navy) 0%, var(--blue) 60%, var(--blue-mid) 100%);
    clip-path: polygon(0 0, 100% 0, 100% 80%, 0 100%);
  }
  .brand { position: absolute; left: 34px; top: 34px; display: flex; align-items: center; gap: 14px; text-align: left; }
  .brand-dot { width: 26px; height: 26px; border-radius: 50%; background: var(--sky); }
  .brand-name { font-family: "Oswald", sans-serif; font-weight: 700; font-size: 46px; line-height: 1; color: var(--white); letter-spacing: 1.5px; }
  .brand-license { font-family: "Montserrat", sans-serif; font-weight: 800; font-size: 12px; color: var(--sky-light); margin-top: 5px; letter-spacing: 1px; }

  .person { position: absolute; top: 165px; left: 0; right: 0; }
  .person-name { font-family: "Montserrat", sans-serif; font-weight: 800; font-size: 32px; color: var(--blue); line-height: 1.1; }
  .person-role { font-size: 15px; font-weight: 600; margin-top: 3px; }
  .dots { display: block; margin: 6px auto 0; }
  .contacts { margin-top: 4px; }
  .contact-line { font-size: 15px; line-height: 1.4; }
  .location { font-size: 15px; font-weight: 600; margin-top: 6px; display: flex; justify-content: center; align-items: center; gap: 6px; color: var(--navy); }

  .trust {
    position: absolute; top: 380px; left: 30px; right: 30px; height: 42px;
    background: var(--mist); border-left: 5px solid var(--sky); border-right: 5px solid var(--sky);
    display: flex; align-items: center; justify-content: center; gap: 8px;
    font-family: "Oswald", sans-serif; font-weight: 600; font-size: 18px; letter-spacing: 1.5px;
    color: var(--blue); text-transform: uppercase;
  }

  .band {
    position: absolute; top: 448px; left: 0; right: 0; height: 54px;
    background: var(--blue); color: var(--white);
    font-family: "Montserrat", sans-serif; font-weight: 800; font-size: 30px; line-height: 54px;
  }
  .tagline {
    position: absolute; top: 514px; left: 0; right: 0;
    font-family: "Oswald", sans-serif; font-weight: 500; font-size: 14px; color: var(--blue);
    text-transform: uppercase; letter-spacing: .5px;
  }
  .services {
    position: absolute; top: 548px; left: 40px; right: 40px; list-style: none;
    display: grid; grid-template-columns: 1fr 1fr; row-gap: 6px; column-gap: 12px;
    font-size: 15px; line-height: 1.4; text-align: left;
  }
  .services li { display: flex; align-items: center; gap: 8px; }
  .services li::before { content: ""; width: 8px; height: 8px; flex: none; border-radius: 50%; background: var(--sky); }
  .footer-stripe { position: absolute; left: 0; right: 0; bottom: 0; height: 26px; background: linear-gradient(90deg, var(--blue), var(--sky)); }
</style>
</head>
<body>
<div class="canvas">

  <section class="card card-back" aria-label="Card back">
    <div class="back-mark">
      <div class="back-name"><span class="back-dot"></span>RK WRECKING</div>
      <div class="back-license">LICENSE#4837215</div>
      <div class="back-trust">LICENSED, BONDED, &amp; INSURED</div>
    </div>
    <div class="back-stripe"></div>
  </section>

  <section class="card card-front" aria-label="Card front">
    <div class="header"></div>
    <div class="brand">
      <span class="brand-dot"></span>
      <div>
        <div class="brand-name">RK WRECKING</div>
        <div class="brand-license">LICENSE#4837215</div>
      </div>
    </div>

    <div class="person">
      <h1 class="person-name">Marcello Vandora</h1>
      <p class="person-role">Owner our city state and zip</p>

      <svg class="dots" width="360" height="30" viewBox="0 0 360 30" aria-hidden="true">
        <g fill="#0054aa">
          <circle cx="10" cy="15" r="2.5"/><circle cx="26" cy="15" r="3.5"/><circle cx="44" cy="15" r="4.5"/>
          <circle cx="64" cy="15" r="5.5"/><circle cx="86" cy="15" r="6.5"/><circle cx="110" cy="15" r="7"/>
          <circle cx="250" cy="15" r="7"/><circle cx="274" cy="15" r="6.5"/><circle cx="296" cy="15" r="5.5"/>
          <circle cx="316" cy="15" r="4.5"/><circle cx="334" cy="15" r="3.5"/><circle cx="350" cy="15" r="2.5"/>
          <circle cx="145" cy="15" r="14"/><circle cx="180" cy="15" r="14"/><circle cx="215" cy="15" r="14"/>
        </g>
        <g fill="none" stroke="#fff" stroke-width="1.8" stroke-linecap="round">
          <path d="M139 9 q-2 6 4 12 q6 5 10 2 l-3 -4 -3 2 q-3 -2 -5 -6 l2 -2 -3 -5z" fill="#fff" stroke="none"/>
          <rect x="172" y="10" width="16" height="11" rx="1"/><path d="M172 11 l8 6 8 -6"/>
          <circle cx="215" cy="15" r="7.5"/><path d="M207.5 15 h15 M215 7.5 q-5 7.5 0 15 q5 -7.5 0 -15"/>
        </g>
      </svg>

      <div class="contacts">
        <p class="contact-line">(555) 318-2740</p>
        <p class="contact-line">info@brightlanecrews.com</p>
        <p class="contact-line">Marcellov@brightlanecrews.com</p>
      </div>

      <p class="location">
        <svg width="16" height="20" viewBox="0 0 16 20" aria-hidden="true">
          <path d="M8 19 q-7 -7 -7 -11 a7 7 0 0 1 14 0 q0 4 -7 11z" fill="#0054aa"/>
          <circle cx="8" cy="8" r="2.6" fill="#fff"/>
        </svg>
        Laguna Crest, CA, 92610
      </p>
    </div>

    <div class="trust">
      <svg width="16" height="16" viewBox="0 0 16 16" aria-hidden="true"><path d="M2 8.5 l4 4 8 -9" fill="none" stroke="#0094d4" stroke-width="2.6" stroke-linecap="round" stroke-linejoin="round"/></svg>
      Licensed, Bonded, &amp; Insured
      <svg width="16" height="16" viewBox="0 0 16 16" aria-hidden="true"><path d="M2 8.5 l4 4 8 -9" fill="none" stroke="#0094d4" stroke-width="2.6" stroke-linecap="round" stroke-linejoin="round"/></svg>
    </div>

    <div class="band">R Wrecking</div>
    <p class="tagline">R Wrecking Selective Demolition &amp; Full Demolition</p>
    <ul class="services">
      <li>Sheds</li>
      <li>Bathrooms</li>
      <li>Digging</li>
      <li>AD Preparation</li>
      <li>Kitchens</li>
      <li>Interiors &amp; Exteriors Demo</li>
    </ul>
    <div class="footer-stripe"></div>
  </section>

</div>
</body>
</html>
```